MRT Property - Business Cards

Looking for a business card & general letterhead, signage etc design for our new logo.

Colours:
000a20
0056a2
00b5ef
0088ce
68cef2

Fonts:
Poppins
Karla

Please keep look and feel of new brand - example in the zip package I sent.

```html
<!DOCTYPE html>
<html lang="en">
<head>
<meta charset="utf-8">
<title>MRT Property – Stationery</title>
<link rel="stylesheet" href="https://fonts.googleapis.com/css2?family=Poppins:wght@400;600;700&display=swap">
<style>
  :root{
    --navy:#000a20;
    --notebook:#10152b;
    --blue:#0056a2;
    --cyan:#00b5ef;
    --mid:#0088ce;
    --sky:#68cef2;
    --paper:#e4e6e6;
    --ink:#1d1d1f;
    --backdrop:#8b8b8b;
  }
  *{box-sizing:border-box;margin:0;padding:0}
  html,body{width:1200px;height:686px;overflow:hidden}
  body{background:var(--backdrop);font-family:"Poppins",sans-serif;position:relative}

  .brand-name{font-family:"Poppins",sans-serif;font-weight:700;color:var(--blue);letter-spacing:.5px;white-space:nowrap;display:flex;align-items:center;gap:8px}
  .brand-name .dot{width:12px;height:12px;border-radius:50%;background:var(--cyan)}

  /* Notebook cover */
  .notebook{position:absolute;left:40px;top:40px;width:420px;height:300px;background:var(--notebook);border-radius:3px}
  .notebook .spiral{position:absolute;top:-8px;left:24px;right:24px;display:flex;justify-content:space-between}
  .notebook .ring{width:10px;height:22px;border:2px solid #2b2d33;border-radius:5px;background:var(--backdrop)}
  .notebook .brand-name{position:absolute;left:30px;bottom:30px;color:#fff;font-size:24px}
  .notebook .brand-name .dot{background:var(--sky)}

  /* Business card */
  .card{position:absolute;left:40px;top:380px;width:320px;height:190px;background:var(--paper);padding:20px 22px;display:flex;flex-direction:column;align-items:flex-end;text-align:right}
  .card .brand-name{font-size:20px}
  .card .address{margin-top:14px;font-size:9.5px;line-height:1.45;color:var(--ink)}
  .card .contacts{margin-top:10px;font-size:9.5px;line-height:1.6;color:var(--ink);list-style:none}
  .card .contacts li{display:flex;justify-content:flex-end;align-items:center;gap:6px}

  .icon{width:9px;height:9px;flex:none}

  /* Envelope */
  .envelope{position:absolute;left:380px;top:380px;width:330px;height:190px;background:var(--blue)}
  .envelope .flap{position:absolute;left:0;top:0;width:100%;height:100%}
  .envelope .brand-name{position:absolute;left:50%;top:58px;transform:translateX(-50%);color:#fff;font-size:13px}

  /* Letterhead */
  .letterhead{position:absolute;left:740px;top:40px;width:420px;height:594px;background:var(--paper);padding:34px 30px}
  .letterhead .brand-name{position:absolute;right:30px;top:34px;font-size:22px}
  .letterhead .contact-block{position:absolute;right:30px;top:96px;border-left:2px solid var(--mid);padding-left:10px;font-size:9.5px;line-height:1.55}
  .letterhead .contacts{list-style:none;color:var(--ink)}
  .letterhead .contacts li{display:flex;align-items:center;gap:6px}
  .letterhead .address{color:var(--mid);display:flex;gap:6px;margin-top:2px}
</style>
</head>
<body>

<section class="notebook" aria-label="Notebook cover">
  <div class="spiral">
    <span class="ring"></span><span class="ring"></span><span class="ring"></span><span class="ring"></span><span class="ring"></span><span class="ring"></span><span class="ring"></span><span class="ring"></span><span class="ring"></span><span class="ring"></span><span class="ring"></span><span class="ring"></span><span class="ring"></span><span class="ring"></span><span class="ring"></span><span class="ring"></span><span class="ring"></span><span class="ring"></span>
  </div>
  <div class="brand-name"><span class="dot"></span>MRT Property</div>
</section>

<section class="card" aria-label="Business card">
  <div class="brand-name"><span class="dot"></span>MRT Property</div>
  <p class="address">Suite 4.12, Tower 3<br>18 Harbourline Road, Sydney,<br>Riverside Park NSW 2140</p>
  <ul class="contacts">
    <li>+61 2 9310 4400
      <svg class="icon" viewBox="0 0 10 10"><path d="M2 1l2 2-1 1.2a6 6 0 0 0 2.8 2.8L7 6l2 2-1.2 1.2C4.5 9 1 5.5.8 2.2z" fill="var(--mid)"/></svg></li>
    <li>www.mrtproperty.com.au
      <svg class="icon" viewBox="0 0 10 10"><circle cx="5" cy="5" r="4.3" fill="none" stroke="var(--mid)" stroke-width="1.2"/><path d="M.8 5h8.4M5 .7c2 2.5 2 6.1 0 8.6M5 .7c-2 2.5-2 6.1 0 8.6" stroke="var(--mid)" fill="none" stroke-width=".8"/></svg></li>
    <li>info@mrtproperty.com.au
      <svg class="icon" viewBox="0 0 10 10"><rect x=".5" y="2" width="9" height="6.5" fill="var(--mid)"/><path d="M.8 2.3L5 5.6l4.2-3.3" stroke="#fff" fill="none" stroke-width=".8"/></svg></li>
  </ul>
</section>

<section class="envelope" aria-label="Envelope">
  <svg class="flap" viewBox="0 0 330 190" preserveAspectRatio="none">
    <path d="M0 0L30 92H300L330 0" fill="#0a4f96" stroke="#08467f" stroke-width="1.5"/>
  </svg>
  <div class="brand-name">MRT Property</div>
</section>

<section class="letterhead" aria-label="Letterhead">
  <div class="brand-name"><span class="dot"></span>MRT Property</div>
  <div class="contact-block">
    <ul class="contacts">
      <li><svg class="icon" viewBox="0 0 10 10"><path d="M2 1l2 2-1 1.2a6 6 0 0 0 2.8 2.8L7 6l2 2-1.2 1.2C4.5 9 1 5.5.8 2.2z" fill="var(--mid)"/></svg>+61 2 9310 4400</li>
      <li><svg class="icon" viewBox="0 0 10 10"><circle cx="5" cy="5" r="4.3" fill="none" stroke="var(--mid)" stroke-width="1.2"/><path d="M.8 5h8.4M5 .7c2 2.5 2 6.1 0 8.6M5 .7c-2 2.5-2 6.1 0 8.6" stroke="var(--mid)" fill="none" stroke-width=".8"/></svg>www.mrtproperty.com.au</li>
      <li><svg class="icon" viewBox="0 0 10 10"><rect x=".5" y="2" width="9" height="6.5" fill="var(--mid)"/><path d="M.8 2.3L5 5.6l4.2-3.3" stroke="#fff" fill="none" stroke-width=".8"/></svg>info@mrtproperty.com.au</li>
    </ul>
    <div class="address">
      <svg class="icon" viewBox="0 0 10 10" style="margin-top:3px"><path d="M5 9.6S1.6 6 1.6 3.8a3.4 3.4 0 0 1 6.8 0C8.4 6 5 9.6 5 9.6z" fill="var(--mid)"/><circle cx="5" cy="3.8" r="1.3" fill="#fff"/></svg>
      <p>Suite 4.12, Tower 3<br>18 Harbourline Road, Sydney,<br>Riverside Park NSW 2140</p>
    </div>
  </div>
</section>

</body>
</html>
```